Maranoola Wines - web page for new Australian wine label

We need a landing page for our wine company. Maranoola is a family owned company, we grow the gapes, and make the wine in the Clare valley. Daniel Whitlock is the winemaker and is well known for his style, which is all about the fruit flavour rather than wood or age influences. Maranoola is Abriginal for 2 hills and a water source. We hand pick, hand plunge, foot crush resulting in elegant wine. Little to no additives, minimal filtering, single vineyard wines. Handcrafted with small releases of only the best fruit from carefully selected rows and bunches. The Clare valley is located two hours North of Adelaide, is known for cool climate and slow ripening, resulting in wines that have an elegant mouth feel, with bright colour and outstanding flavours. Our Brookmere vineyard has a Eastern aspect, gathering morning sun and escaping the hot afternoons, and in our opinion is on of the prettiest valleys in the world. Only 1000 cases per annum of the very best handpicked fruit, from the best rows. We hope you enjoy the Maranoola style, the reds are lighter in colour, fruit driven palate, more old world influence and the Riesling is on the dry side with fresh citrus. Minimal additives and filtering, our aim was to make wine with minimal influence from wine making. Handcrafted wines.

Target Market(s)

females 18 - 60 are the ones that buy 70 percent of wine, so whilst men are also a target, its the ladies we seek to appeal to.

Industry/Entity Type

It Company

Number of Pages Required

4 page

Font styles to use
Serif

Requirements
Must have
• Eye catching front page that makes me feel like i am ordering from quality company, that cares for what they do. Easy to use ordering, and delivery instructions.
• postage is $14.90 per case Australia wide.
• www.maranoolawines-example.com
Nice to have
• I want to see a fun and family oriented business that cares for the wine, we dont make a lot, its buckets and feet. But its wine made wanting to be the best in the world, we dont cut corners on quality. Handcrafted
Should not have
• dont really have any thoughts here, looking for all ideas

```html
<!DOCTYPE html>
<html lang="en">
<head>
<meta charset="utf-8">
<title>Maranoola Wines</title>
<link href="https://fonts.googleapis.com/css2?family=Great+Vibes&family=Open+Sans:wght@400;600&family=Roboto:wght@400;500;700&family=Lora:ital@1&display=swap" rel="stylesheet">
<style>
:root{
  --blue:#0a6ab6;
  --blue-dark:#075a9c;
  --text:#6d6d6d;
  --heading:#333;
  --footer-bg:#f4f5f7;
  --bar-bg:#333333;
  --white:#fff;
  --ring:#d9d9d9;
}
*{margin:0;padding:0;box-sizing:border-box}
html,body{width:1200px;height:2378px;overflow:hidden;background:var(--white)}
body{position:relative;font-family:"Open Sans",Arial,sans-serif;color:var(--text)}
.script{font-family:"Great Vibes",cursive}

/* header */
.site-header{position:absolute;top:0;left:0;width:1200px;height:87px;display:flex;align-items:center}
.brand{position:absolute;left:87px;top:22px;font-family:"Roboto",Arial,sans-serif;font-size:36px;font-weight:400;color:var(--blue);letter-spacing:1px}
.main-nav{position:absolute;top:0;left:452px;height:87px;display:flex;align-items:center;gap:0}
.main-nav a{font-family:"Roboto",Arial,sans-serif;font-size:12.5px;text-transform:uppercase;color:#333;text-decoration:none;position:absolute;white-space:nowrap;top:36px}
.main-nav a.active{color:var(--blue)}
.search-btn{position:absolute;left:1068px;top:22px;width:45px;height:45px;border-radius:50%;background:var(--blue);display:flex;align-items:center;justify-content:center}

/* hero */
.hero{position:absolute;top:87px;left:0;width:1200px;height:528px}
.hero-photo{position:absolute;inset:0;background:linear-gradient(120deg,#3d3a3f 0%,#5b5560 35%,#7a6a70 60%,#4a3236 100%)}
.hero-arrow{position:absolute;top:236px;width:54px;height:54px;border:2px solid var(--white);border-radius:50%;display:flex;align-items:center;justify-content:center}
.hero-arrow.prev{left:24px}
.hero-arrow.next{left:1121px}
.hero-caption{position:absolute;left:777px;top:300px;width:350px;color:var(--white)}
.hero-caption h1{font-family:"Great Vibes",cursive;font-weight:400;font-size:72px;line-height:1;margin-bottom:14px}
.hero-caption p{font-family:Arial,sans-serif;font-size:12.5px;line-height:22px}

/* sections */
.section-title{position:absolute;left:0;width:1200px;text-align:center;font-family:"Great Vibes",cursive;font-weight:400;font-size:48px;color:#777}
.section-title span{color:var(--blue)}
.section-lead{position:absolute;left:235px;width:730px;text-align:center;font-size:12.5px;line-height:23px}

.feature{position:absolute;top:790px;width:250px;text-align:center}
.feature-photo{width:146px;height:146px;margin:0 auto;border-radius:50%;border:1px solid var(--ring);padding:5px}
.feature-photo div{width:100%;height:100%;border-radius:50%}
.feature h3{margin-top:22px;font-family:"Roboto",Arial,sans-serif;font-weight:500;font-size:16.5px;color:var(--blue);text-transform:uppercase}
.feature p{margin-top:8px;font-size:12px;line-height:22px}

.services{position:absolute;top:1075px;left:0;width:1200px;height:393px;background:var(--blue)}
.services-photo{position:absolute;left:0;top:0;width:515px;height:393px;background:linear-gradient(180deg,#8fb4d6 0%,#c8d8e2 35%,#e6e2d8 60%,#d9cfc2 100%)}
.services-body{position:absolute;left:583px;top:62px;width:470px;color:var(--white)}
.services-body h2{font-family:"Great Vibes",cursive;font-weight:400;font-size:44px;margin-bottom:14px}
.services-body p{font-family:Arial,sans-serif;font-size:12px;line-height:25px}
.services-body a{display:inline-block;margin-top:20px;color:var(--white);font-family:"Roboto",Arial,sans-serif;font-weight:700;font-size:14px;text-decoration:underline}

.post{position:absolute;top:1645px;width:328px}
.post-photo{width:328px;height:197px}
.post h3{margin-top:25px;font-family:"Roboto",Arial,sans-serif;font-weight:400;font-size:15px;color:var(--heading);text-transform:uppercase}
.post p{margin-top:14px;font-family:Arial,sans-serif;font-size:12px;line-height:22px}
.post-meta{margin-top:10px;display:flex;align-items:center;gap:6px;font-family:"Lora",serif;font-style:italic;font-size:13px;color:var(--blue)}
.post-meta span{margin-right:8px}

/* footer */
.site-footer{position:absolute;top:2032px;left:0;width:1200px;height:276px;background:var(--footer-bg)}
.footer-brand{position:absolute;left:92px;top:104px;font-family:"Roboto",Arial,sans-serif;font-size:44px;font-weight:400;color:var(--blue);letter-spacing:1px}
.footer-col{position:absolute;top:48px}
.footer-col h4{font-family:"Roboto",Arial,sans-serif;font-weight:500;font-size:16px;color:#444;text-transform:uppercase;margin-bottom:20px}
.contact-list{list-style:none}
.contact-list li{display:flex;align-items:flex-start;gap:12px;font-family:Arial,sans-serif;font-size:12.5px;color:#444;line-height:18px;margin-bottom:11px}
.contact-list a{color:#444}
.contact-list svg{flex:none;margin-top:2px}
.newsletter p{font-size:12.5px;line-height:20px;color:#555;width:220px}
.email-field{margin-top:16px;width:211px;height:32px;border:1px solid #d6d6d6;background:var(--white);font-size:12px;color:#777;padding:8px 14px}
.subscribe{margin-top:16px;width:82px;height:28px;background:var(--blue);color:var(--white);font-size:10px;font-weight:600;text-transform:uppercase;display:flex;align-items:center;justify-content:center}
.follow p{font-size:11.5px;line-height:18px;color:#666;width:210px}
.social{margin-top:18px;display:flex;gap:8px}
.social span{width:35px;height:35px;border:1px solid #bbb;border-radius:50%}

.copyright{position:absolute;top:2308px;left:0;width:1200px;height:70px;background:var(--bar-bg);color:var(--white);font-family:Arial,sans-serif;font-size:12px;display:flex;align-items:center;justify-content:center}
</style>
</head>
<body>

<header class="site-header">
  <div class="brand">Maranoola</div>
  <nav class="main-nav" style="left:0">
    <a class="active" href="#" style="left:452px">Home</a>
    <a href="#" style="left:527px">About Us</a>
    <a href="#" style="left:624px">Services</a>
    <a href="#" style="left:718px">Products</a>
    <a href="#" style="left:818px">News</a>
    <a href="#" style="left:894px">Gallery</a>
    <a href="#" style="left:986px">Contact Us</a>
  </nav>
  <div class="search-btn">
    <svg width="14" height="14" viewBox="0 0 14 14"><circle cx="6" cy="6" r="4" fill="none" stroke="#fff" stroke-width="2"/><line x1="9" y1="9" x2="12.5" y2="12.5" stroke="#fff" stroke-width="2"/></svg>
  </div>
</header>

<section class="hero">
  <div class="hero-photo" role="img" aria-label="Photo of two children foot-crushing grapes in a red tub at the winery"></div>
  <div class="hero-arrow prev"><svg width="16" height="16" viewBox="0 0 16 16"><polyline points="10,2 4,8 10,14" fill="none" stroke="#fff" stroke-width="2.5"/></svg></div>
  <div class="hero-arrow next"><svg width="16" height="16" viewBox="0 0 16 16"><polyline points="6,2 12,8 6,14" fill="none" stroke="#fff" stroke-width="2.5"/></svg></div>
  <div class="hero-caption">
    <h1>Maranoola</h1>
    <p>Sed ut perspiciatis unde omnis iste natus error sit voluptatem accusantium doloremque laudantium, totam rem aperiam, eaq ue ipsa quae ab illo inventore veritatis</p>
  </div>
</section>

<h2 class="section-title" style="top:648px">Welcome To <span>Maranoola</span></h2>
<p class="section-lead" style="top:713px">Sed ut perspiciatis unde omnis iste natus error sit voluptatem accusantium doloremque laudantium, totam rem aperiam, eaque ipsa quae ab illo inventore veritatis et quasi architecto beatae vitae dicta sunt explicabo.</p>

<div class="feature" style="left:86px">
  <div class="feature-photo"><div role="img" aria-label="Photo of a picker harvesting grapes by hand among the vines" style="background:linear-gradient(160deg,#5f7a3a,#8a4a2e)"></div></div>
  <h3>Hand Pick</h3>
  <p>Sed ut perspiciatis unde omnis iste nat beatae vit dicta sunt explicabo.</p>
</div>
<div class="feature" style="left:344px">
  <div class="feature-photo"><div role="img" aria-label="Photo of the winemakers among barrels in the cellar" style="background:linear-gradient(160deg,#3a3430,#7a6048)"></div></div>
  <h3>Hand Plunge</h3>
  <p>Sed ut perspiciatis unde omnis iste nat beatae vit dicta sunt explicabo.</p>
</div>
<div class="feature" style="left:603px">
  <div class="feature-photo"><div role="img" aria-label="Photo of crushed grapes being worked by hand" style="background:linear-gradient(160deg,#4a2a3a,#7a5a6a)"></div></div>
  <h3>Foot Crush Resulting</h3>
  <p>Sed ut perspiciatis unde omnis iste nat beatae vit dicta sunt explicabo.</p>
</div>
<div class="feature" style="left:861px">
  <div class="feature-photo"><div role="img" aria-label="Photo of ripe grape bunches on the vine" style="background:linear-gradient(160deg,#3e5a2a,#2a2a3a)"></div></div>
  <h3>Elegant Wine</h3>
  <p>Sed ut perspiciatis unde omnis iste nat beatae vit dicta sunt explicabo.</p>
</div>

<section class="services">
  <div class="services-photo" role="img" aria-label="Photo of a bottle of Maranoola wine beside a bowl of crayfish on a beach"></div>
  <div class="services-body">
    <h2>Our Services</h2>
    <p>Sed ut perspiciatis unde omnis iste natus error sit voluptatem accusantium dolorem que laudantium, totam rem aperiam, eaque ipsa quae ab illo inventore veritatis et qu asi architecto beatae vitae dicta sunt explicabo. Nemo enim ipsam voluptatem quia voluptas sit aspernatur aut odit aut fugit, sed quia consequuntur magni dolores eos qui ratione voluptatem sequi nesciunt.</p>
    <a href="#">DELIVERY CHARGE IS $14.90 PER</a>
  </div>
</section>

<h2 class="section-title" style="top:1507px"><span style="color:#777">Latest</span> <span>Blog</span></h2>
<p class="section-lead" style="top:1572px">Sed ut perspiciatis unde omnis iste natus error sit voluptatem accusantium doloremque laudantium, totam rem aperiam, eaque ipsa quae ab illo inventore veritatis et quasi architecto beatae vitae dicta sunt explicabo.</p>

<article class="post" style="left:87px">
  <div class="post-photo" role="img" aria-label="Photo of two winemakers tasting wine among cellar barrels" style="background:linear-gradient(150deg,#3c3530,#6e5a45 60%,#a08a6a)"></div>
  <h3>Neque Porro Quisquam</h3>
  <p>Sed ut perspiciatis unde omnis iste natus error sit voluptatem accusantiumue ipsa beatae vitae dicta sunt explicabo.</p>
  <div class="post-meta">
    <svg width="12" height="12" viewBox="0 0 12 12"><rect x="1" y="2" width="10" height="9" fill="none" stroke="#0a6ab6" stroke-width="1.3"/><line x1="1" y1="5" x2="11" y2="5" stroke="#0a6ab6" stroke-width="1.3"/></svg><span>1 month ago</span>
    <svg width="13" height="12" viewBox="0 0 13 12"><path d="M1.5 2h10v6h-6l-3 2.5V8h-1z" fill="none" stroke="#0a6ab6" stroke-width="1.3"/></svg><span>05 Comments</span>
  </div>
</article>
<article class="post" style="left:436px">
  <div class="post-photo" role="img" aria-label="Photo of the picking crew gathered in the vineyard" style="background:linear-gradient(180deg,#9fb7cc,#6f7f4a 50%,#8a7a5a)"></div>
  <h3>Neque Porro Quisquam</h3>
  <p>Sed ut perspiciatis unde omnis iste natus error sit voluptatem accusantiumue ipsa beatae vitae dicta sunt explicabo.</p>
  <div class="post-meta">
    <svg width="12" height="12" viewBox="0 0 12 12"><rect x="1" y="2" width="10" height="9" fill="none" stroke="#0a6ab6" stroke-width="1.3"/><line x1="1" y1="5" x2="11" y2="5" stroke="#0a6ab6" stroke-width="1.3"/></svg><span>1 month ago</span>
    <svg width="13" height="12" viewBox="0 0 13 12"><path d="M1.5 2h10v6h-6l-3 2.5V8h-1z" fill="none" stroke="#0a6ab6" stroke-width="1.3"/></svg><span>05 Comments</span>
  </div>
</article>
<article class="post" style="left:785px">
  <div class="post-photo" role="img" aria-label="Photo of two children crushing grapes in a red tub" style="background:linear-gradient(140deg,#4a4550,#6a5a62 50%,#8a3a40)"></div>
  <h3>Neque Porro Quisquam</h3>
  <p>Sed ut perspiciatis unde omnis iste natus error sit voluptatem accusantiumue ipsa beatae vitae dicta sunt explicabo.</p>
  <div class="post-meta">
    <svg width="12" height="12" viewBox="0 0 12 12"><rect x="1" y="2" width="10" height="9" fill="none" stroke="#0a6ab6" stroke-width="1.3"/><line x1="1" y1="5" x2="11" y2="5" stroke="#0a6ab6" stroke-width="1.3"/></svg><span>1 month ago</span>
    <svg width="13" height="12" viewBox="0 0 13 12"><path d="M1.5 2h10v6h-6l-3 2.5V8h-1z" fill="none" stroke="#0a6ab6" stroke-width="1.3"/></svg><span>05 Comments</span>
  </div>
</article>

<footer class="site-footer">
  <div class="footer-brand">Maranoola</div>

  <div class="footer-col" style="left:390px">
    <h4>Contact Us</h4>
    <ul class="contact-list">
      <li><svg width="14" height="12" viewBox="0 0 14 12"><path d="M1 4c0-2 2-3 6-3s6 1 6 3l-3 1-1-2H5L4 5z M3 6h8l1 5H2z" fill="#777"/></svg>(000)-121-1231 (Phone)</li>
      <li><svg width="14" height="12" viewBox="0 0 14 12"><rect x="3" y="0" width="8" height="4" fill="#777"/><rect x="0" y="4" width="14" height="6" rx="1" fill="#777"/><rect x="3" y="8" width="8" height="4" fill="#999"/></svg>(000)-121-1231 (Fax)</li>
      <li><svg width="14" height="11" viewBox="0 0 14 11"><rect x="0" y="0" width="14" height="11" fill="#777"/><polyline points="0,0 7,6 14,0" fill="none" stroke="#f4f5f7" stroke-width="1.3"/></svg><a href="#">info@maranoola.com</a></li>
      <li><svg width="14" height="14" viewBox="0 0 14 14"><path d="M7 13C4 9 3 7 3 5a4 4 0 0 1 8 0c0 2-1 4-4 8z" fill="#777"/><circle cx="7" cy="5" r="1.5" fill="#f4f5f7"/></svg>#24 Lorem Ipsum Dummy<br>Lorem Ipsum</li>
    </ul>
  </div>

  <div class="footer-col newsletter" style="left:650px">
    <h4>Newsletter</h4>
    <p>Register Your email address to get information about us</p>
    <div class="email-field">Email Address</div>
    <div class="subscribe">Subscribe</div>
  </div>

  <div class="footer-col follow" style="left:908px">
    <h4>Follow Us</h4>
    <p>Lorem ipsum dolor sit amet, conse ctetur adipiscing elit. Nulla in purus nibh. Donec ornare</p>
    <div class="social"><span></span><span></span><span></span><span></span><span></span></div>
  </div>
</footer>

<div class="copyright">© Copyright 2017 Maranoola.All Rights Reserved</div>

</body>
</html>
```